Harborline Renewal Business Card Design

Professional and clean design. The design colors should flow with the logo. Two-sided card with the website on the back which is:

www.HarborlineRenewal.example.

"Specializing in Water Damage Restoration"

On the front I need the name, email, phone, and logo.

Name: Darnell Quisby
Email: Darnell@HarborlineRenewal.example
Phone: 555-318-2046 for now

I only have the Preview and Thumbnail right now but should have the source files uploaded within a day or two.

Target Market(s)

Flood victims, home owners with water damage from busted pipes etc...

Industry/Entity Type

Business

Contact Information for Business Card

Name: Darnell Quisby

Font styles to use
Serif
Sans Serif

Requirements
Must have
• Business Card Details Info

```html
<!DOCTYPE html>
<html lang="en">
<head>
<meta charset="utf-8">
<title>Harborline Renewal Business Card</title>
<link rel="stylesheet" href="https://fonts.googleapis.com/css2?family=Cinzel:wght@500&family=Source+Sans+3:wght@400;600&display=swap">
<style>
  :root {
    --stage: #000000;
    --card-light: #f3f2f2;
    --brand-blue: #2ba3df;
    --sky-top: #55c3f1;
    --sky-bottom: #2d9fdc;
    --ink: #1d1d1d;
    --white: #ffffff;
  }
  * { margin: 0; padding: 0; box-sizing: border-box; }
  html, body {
    width: 1200px; height: 900px; overflow: hidden;
    background: var(--stage);
    font-family: "Source Sans 3", "Segoe UI", sans-serif;
  }
  .stage { position: relative; width: 1200px; height: 900px; }

  .card {
    position: absolute; top: 275px;
    width: 477px; height: 294px; overflow: hidden;
  }

  /* Front */
  .card-front {
    left: 116px;
    background: var(--card-light);
    border-radius: 0 46px 0 46px;
  }
  .brand-mark {
    position: absolute; left: 107px; top: 33px;
    width: 70px; height: 70px; border-radius: 50%;
    background: var(--brand-blue);
  }
  .brand-name {
    position: absolute; left: 0; width: 284px; text-align: center;
    font-family: "Cinzel", "Times New Roman", serif; font-weight: 500;
    text-transform: uppercase; letter-spacing: 1px; white-space: nowrap;
  }
  .card-front .brand-name { top: 112px; font-size: 22px; color: var(--brand-blue); }

  .name-rule {
    position: absolute; top: 195px; height: 2px; background: var(--brand-blue);
  }
  .name-rule.left { left: 0; width: 292px; }
  .name-rule.right { left: 446px; width: 31px; }
  .person-name {
    position: absolute; left: 300px; top: 183px;
    font-size: 17px; font-weight: 600; color: var(--brand-blue); white-space: nowrap;
  }
  .contact {
    position: absolute; right: 33px;
    display: flex; align-items: center; gap: 6px;
    font-size: 13px; color: var(--ink); white-space: nowrap;
  }
  .contact svg { width: 10px; height: 10px; fill: var(--brand-blue); }
  .contact.phone { top: 227px; }
  .contact.email { top: 247px; }

  /* Back */
  .card-back {
    left: 622px;
    background: var(--white);
    border-radius: 46px 0 46px 0;
  }
  .sky-band {
    position: absolute; left: 0; top: 0; width: 100%; height: 235px;
    background: linear-gradient(180deg, var(--sky-top), var(--sky-bottom));
  }
  .card-back .brand-name {
    width: 100%; top: 128px; font-size: 30px; color: var(--white);
  }
  .website {
    position: absolute; width: 100%; top: 198px; text-align: center;
    font-size: 13px; font-weight: 600; color: var(--white);
  }
  .tagline {
    position: absolute; width: 100%; top: 252px; text-align: center;
    font-size: 15px; font-weight: 600; color: var(--brand-blue);
  }
</style>
</head>
<body>
<main class="stage">
  <section class="card card-front" aria-label="Card front">
    <div class="brand-mark"></div>
    <div class="brand-name">Harborline Renewal</div>
    <div class="name-rule left"></div>
    <div class="person-name">Darnell Quisby</div>
    <div class="name-rule right"></div>
    <div class="contact phone">555-318-2046
      <svg viewBox="0 0 24 24" aria-hidden="true"><path d="M6.6 10.8a15.2 15.2 0 0 0 6.6 6.6l2.2-2.2a1 1 0 0 1 1-.25 11.4 11.4 0 0 0 3.6.57 1 1 0 0 1 1 1V20a1 1 0 0 1-1 1A17 17 0 0 1 3 4a1 1 0 0 1 1-1h3.5a1 1 0 0 1 1 1c0 1.25.2 2.45.57 3.57a1 1 0 0 1-.25 1z"/></svg>
    </div>
    <div class="contact email">Darnell@HarborlineRenewal.example
      <svg viewBox="0 0 24 24" aria-hidden="true"><path d="M2 5h20v14H2z M3.5 6.5 12 13l8.5-6.5" fill-rule="evenodd"/><path d="M3 6l9 7 9-7" fill="none" stroke="#f3f2f2" stroke-width="2"/></svg>
    </div>
  </section>

  <section class="card card-back" aria-label="Card back">
    <div class="sky-band"></div>
    <div class="brand-name">Harborline Renewal</div>
    <div class="website">www.HarborlineRenewal.example</div>
    <div class="tagline">Specializing in Water Damage Restoration</div>
  </section>
</main>
</body>
</html>
```